QVR business card

Need a business card for a company that provides instructional design and elearning development services. The website is here: http://quorvane.studio/

I'm attaching a current logo, as well as the old business card design. While I like to keep it clean, the old design is too simplistic for my liking. The only idea I want to reuse from the old design is placing industry jargon on the back of the card, just need a better way to present it. But if you have other ideas for the back--feel free to experiment.

Please use the colors complementary to the color we have on the website. Thank you!

```html
<!DOCTYPE html>
<html lang="en">
<head>
<meta charset="utf-8">
<title>QVR business card</title>
<link rel="stylesheet" href="https://fonts.googleapis.com/css2?family=Open+Sans:wght@400;600;700&display=swap">
<style>
  :root {
    --teal: #35b5ae;
    --gold: #c6b57e;
    --ink: #444444;
    --paper: #ffffff;
    --paper-shade: #e6e6e6;
    --slate: #5a5a5a;
    --slate-deep: #333333;
    --line: #f2f2f2;
    --backdrop: #d4d4d4;
  }
  * { box-sizing: border-box; margin: 0; padding: 0; }
  html, body { width: 1200px; height: 900px; overflow: hidden; }
  body {
    background: var(--backdrop);
    font-family: "Open Sans", Arial, sans-serif;
    position: relative;
  }
  .card {
    position: absolute;
    left: 290px;
    width: 620px;
    height: 354px;
    overflow: hidden;
  }
  .card--front { top: 72px; background: linear-gradient(100deg, var(--paper) 40%, var(--paper-shade)); }
  .card--back { top: 474px; background: linear-gradient(100deg, var(--slate) 0%, var(--slate-deep) 100%); }

  .brand { position: absolute; display: flex; align-items: center; gap: 14px; }
  .brand__square { width: 40px; height: 40px; background: var(--teal); }
  .brand__name { font-weight: 700; color: var(--gold); font-size: 58px; line-height: 1; letter-spacing: 2px; }
  .card--front .brand { left: 52px; top: 52px; }
  .card--back .brand { left: 50%; transform: translateX(-50%); top: 30px; }

  .accent { position: absolute; }
  .accent--teal { left: 0; top: 214px; width: 62px; height: 46px; background: var(--teal); }
  .accent--gold { right: 0; top: 152px; width: 62px; height: 42px; background: var(--gold); }

  .holder {
    position: absolute; left: 0; right: 0; top: 186px;
    text-align: center; font-weight: 600; font-size: 26px; color: var(--ink);
  }
  .contact { position: absolute; font-size: 14px; color: var(--ink); letter-spacing: 0.6px; }
  .contact b { color: var(--teal); font-weight: 700; }
  .contact--phone { left: 250px; top: 268px; }
  .contact--lines { left: 34px; top: 306px; }

  .help { position: absolute; left: 0; right: 0; top: 120px; height: 30px; }
  .help__rule { position: absolute; top: 14px; height: 3px; background: var(--line); }
  .help__rule--left { left: 0; width: 170px; }
  .help__rule--right { right: 0; width: 170px; }
  .help__title {
    position: absolute; left: 0; right: 0; top: 0; text-align: center;
    color: var(--gold); font-weight: 600; font-size: 21px; letter-spacing: 1px;
  }
  .jargon {
    position: absolute; color: var(--teal); font-size: 15px; line-height: 26px;
    letter-spacing: 0.8px; text-transform: uppercase;
  }
  .jargon span { margin-right: 14px; }
  .jargon--left { left: 44px; top: 172px; }
  .jargon--right { right: 40px; top: 206px; text-align: left; }
</style>
</head>
<body>
  <section class="card card--front" aria-label="Card front">
    <div class="brand"><span class="brand__square"></span><span class="brand__name">QVR</span></div>
    <div class="accent accent--gold"></div>
    <div class="accent accent--teal"></div>
    <p class="holder">Marta Velloso</p>
    <p class="contact contact--phone"><b>T.</b> 555-013-4827</p>
    <p class="contact contact--lines"><b>E.</b> mvelloso@quorvane.studio | <b>W.</b> www.quorvane.studio</p>
  </section>

  <section class="card card--back" aria-label="Card back">
    <div class="brand"><span class="brand__square"></span><span class="brand__name">QVR</span></div>
    <div class="help">
      <span class="help__rule help__rule--left"></span>
      <h2 class="help__title">HOW CAN WE HELP?</h2>
      <span class="help__rule help__rule--right"></span>
    </div>
    <p class="jargon jargon--left">
      <span>Mobile</span><span>Learning</span><span>SCORM</span><br>
      <span>Instructional Design</span><span>LMS</span><br>
      <span>MOOCs</span><span>eLearning</span><span>HTML5</span>
    </p>
    <p class="jargon jargon--right">
      <span>Adult</span><span>Learning</span><span>Theory</span><br>
      <span>Gamification</span><span>Classroom</span><br>
      <span>xAPI</span><span>Blended</span><span>Learning</span>
    </p>
  </section>
</body>
</html>
```